TALMORK

The business want a professional looking business card. We have a scetch we will add but want the extra upgrade, and would like more suggestions for variations of our business cards.

```html
<!DOCTYPE html>
<html lang="en">
<head>
<meta charset="utf-8">
<title>TALMORK Business Card</title>
<link href="https://fonts.googleapis.com/css2?family=Cinzel:wght@500;700&family=Playfair+Display:wght@600&family=Outfit:wght@400;500&display=swap" rel="stylesheet">
<style>
  :root{
    --stage:#95856a;
    --card-dark:#170e03;
    --card-mid:#37270a;
    --gold:#d8b760;
    --gold-soft:#b8953f;
    --gold-deep:#7a5a1c;
    --ink-light:#ece4cf;
  }
  *{margin:0;padding:0;box-sizing:border-box}
  html,body{width:1200px;height:1200px;overflow:hidden;background:var(--stage)}
  .canvas{position:relative;width:1200px;height:1200px}
  .card{position:absolute;left:180px;width:840px;height:480px;overflow:hidden;background:var(--card-dark);box-shadow:0 24px 40px rgba(40,28,10,.45)}
  .card--front{top:78px}
  .card--back{top:630px}
  .tone-panel{position:absolute;inset:0;background:var(--card-mid)}
  .card--front .tone-panel{clip-path:polygon(0 0,452px 0,340px 480px,0 480px)}
  .card--back .tone-panel{clip-path:polygon(380px 0,840px 0,840px 480px,516px 480px)}
  .rule{position:absolute;background:var(--gold-soft)}
  .rule--h{height:1px}
  .rule--v{width:1px}
  .ornament{position:absolute}
  .ornament--top-left{left:0;top:0;width:184px;height:178px;background:radial-gradient(circle at 0 0,var(--gold) 0%,var(--gold-soft) 45%,rgba(184,149,63,0) 72%)}
  .ornament--bottom-right{right:0;bottom:0;width:184px;height:182px;background:radial-gradient(circle at 100% 100%,var(--gold) 0%,var(--gold-soft) 45%,rgba(184,149,63,0) 72%)}
  .ornament--back-corner{right:0;bottom:0;width:120px;height:118px;background:radial-gradient(circle at 100% 100%,var(--gold) 0%,var(--gold-soft) 45%,rgba(184,149,63,0) 72%)}
  .brand{position:absolute;display:flex;flex-direction:column;align-items:center;transform:translateX(-50%)}
  .brand__dot{width:22px;height:22px;border-radius:50%;background:var(--gold);margin-bottom:26px}
  .brand__name{font-family:"Cinzel",serif;font-weight:500;font-size:40px;letter-spacing:.28em;margin-right:-.28em;color:var(--gold);line-height:1}
  .brand__since{font-family:"Outfit",sans-serif;font-weight:500;font-size:13px;letter-spacing:.45em;margin-right:-.45em;color:var(--gold-soft);margin-top:12px}
  .card--front .brand{left:420px;top:222px}
  .card--back .brand{left:218px;top:228px}
  .company-line{position:absolute;left:37px;top:24px;font-family:"Cinzel",serif;font-weight:700;font-size:22px;letter-spacing:.16em;color:var(--gold-soft)}
  .person{position:absolute;left:396px;top:146px}
  .person__name{font-family:"Playfair Display",serif;font-weight:600;font-size:34px;color:var(--gold);line-height:1.1}
  .person__role{font-family:"Outfit",sans-serif;font-weight:500;font-size:19px;color:var(--ink-light);margin-top:2px}
  .contact-list{position:absolute;left:396px;top:236px;list-style:none}
  .contact-list li{display:flex;align-items:center;height:22px;margin-bottom:24px;font-family:"Outfit",sans-serif;font-weight:500;font-size:19px;color:var(--ink-light)}
  .contact-list li:nth-child(2){margin-bottom:24px}
  .contact-list svg{width:20px;height:20px;margin-right:13px;flex:none}
</style>
</head>
<body>
<div class="canvas">

  <section class="card card--front">
    <div class="tone-panel"></div>
    <div class="rule rule--h" style="left:132px;top:34px;width:674px"></div>
    <div class="rule rule--v" style="left:806px;top:34px;height:312px"></div>
    <div class="rule rule--v" style="left:38px;top:130px;height:312px"></div>
    <div class="rule rule--h" style="left:38px;top:442px;width:674px"></div>
    <div class="ornament ornament--top-left" role="img" aria-label="Gold leaf ornament cluster in the corner"></div>
    <div class="ornament ornament--bottom-right" role="img" aria-label="Gold leaf ornament cluster in the corner"></div>
    <div class="brand">
      <span class="brand__dot"></span>
      <span class="brand__name">TALMORK</span>
      <span class="brand__since">SINCE 2026</span>
    </div>
  </section>

  <section class="card card--back">
    <div class="tone-panel"></div>
    <h1 class="company-line">TALMORK HAUGVIK</h1>
    <div class="rule rule--h" style="left:394px;top:34px;width:412px"></div>
    <div class="rule rule--v" style="left:806px;top:34px;height:313px"></div>
    <div class="rule rule--v" style="left:38px;top:54px;height:388px"></div>
    <div class="rule rule--h" style="left:38px;top:442px;width:674px"></div>
    <div class="ornament ornament--back-corner" role="img" aria-label="Gold leaf ornament cluster in the corner"></div>
    <div class="brand">
      <span class="brand__dot"></span>
      <span class="brand__name">TALMORK</span>
      <span class="brand__since">SINCE 2026</span>
    </div>
    <div class="person">
      <h2 class="person__name">Anders Lien Haugvik</h2>
      <p class="person__role">CEO &amp; Founder</p>
    </div>
    <div class="rule rule--h" style="left:394px;top:225px;width:346px"></div>
    <ul class="contact-list">
      <li>
        <svg viewBox="0 0 24 24" aria-hidden="true"><path d="M6.6 3.5l3 3.2-1.8 2.2a12 12 0 0 0 7.3 7.3l2.2-1.8 3.2 3-1.6 2.6C12 20 4 12 4 5.1z" fill="var(--gold-soft)"/><path d="M14 4a6 6 0 0 1 6 6M14 7.5a2.5 2.5 0 0 1 2.5 2.5" fill="none" stroke="var(--gold-soft)" stroke-width="1.8" stroke-linecap="round"/></svg>
        004791234560
      </li>
      <li>
        <svg viewBox="0 0 24 24" aria-hidden="true"><rect x="2" y="5" width="20" height="14" rx="1.5" fill="var(--gold-soft)"/><path d="M2.5 6l9.5 7 9.5-7" fill="none" stroke="var(--card-mid)" stroke-width="1.6"/></svg>
        talmork.llc@postmail.com
      </li>
      <li>
        <svg viewBox="0 0 24 24" aria-hidden="true" fill="none" stroke="var(--gold-soft)" stroke-width="1.5"><circle cx="12" cy="12" r="9"/><ellipse cx="12" cy="12" rx="4" ry="9"/><path d="M3 12h18M4.5 7.5h15M4.5 16.5h15"/></svg>
        www.talmork.llc
      </li>
    </ul>
  </section>

</div>
</body>
</html>
```